Business card for a new cabinet shop company named Veloran Cabinets for high end cabinets

Design a business card, thinking dark rich green with colours to speak of high end luxury ie; cream, gold, black possibly

Mitchell Tarrowby
Director Craftsman
Email: info@veloranjoinery-example.com.au
Instagram : @veloran.cabinets

```html
<!DOCTYPE html>
<html lang="en">
<head>
<meta charset="utf-8">
<title>Veloran Cabinets – Business Card</title>
<link href="https://fonts.googleapis.com/css2?family=Montserrat:wght@400;500;700&display=swap" rel="stylesheet">
<style>
  :root {
    --backdrop: #9a9a9a;
    --card-green: #006100;
    --gold: #cfad69;
    --cream: #ffffff;
  }
  html, body {
    margin: 0;
    padding: 0;
    width: 1200px;
    height: 1059px;
    overflow: hidden;
    background: var(--backdrop);
    font-family: "Montserrat", Arial, sans-serif;
  }
  .canvas {
    position: relative;
    width: 1200px;
    height: 1059px;
  }
  .card {
    position: absolute;
    background: var(--card-green);
    border-radius: 30px;
    overflow: hidden;
  }
  .card--front { left: 256px; top: 86px; width: 695px; height: 397px; }
  .card--back  { left: 254px; top: 569px; width: 703px; height: 400px; }

  .brand-name {
    position: absolute;
    margin: 0;
    color: var(--gold);
    font-weight: 500;
    line-height: 1.05;
  }
  .card--front .brand-name {
    left: 54px;
    top: 44px;
    font-size: 50px;
    letter-spacing: 1px;
  }
  .brand-mark {
    position: absolute;
    border: 5px solid var(--gold);
    border-radius: 50%;
    box-sizing: border-box;
  }
  .card--front .brand-mark {
    left: 454px; top: 74px; width: 180px; height: 180px;
  }

  .person-name {
    position: absolute;
    left: 41px;
    top: 214px;
    margin: 0;
    font-size: 30px;
    font-weight: 700;
    color: var(--gold);
  }
  .person-role {
    position: absolute;
    left: 41px;
    top: 260px;
    margin: 0;
    font-size: 18px;
    font-weight: 400;
    color: var(--cream);
  }
  .contact-list {
    position: absolute;
    left: 37px;
    top: 300px;
    margin: 0;
    padding: 0;
    list-style: none;
  }
  .contact-item {
    display: flex;
    align-items: center;
    height: 33px;
    font-size: 18px;
    color: var(--cream);
  }
  .contact-icon {
    width: 18px;
    height: 18px;
    margin-right: 8px;
    flex: none;
  }

  .card--back .brand-mark {
    left: 151px; top: 144px; width: 118px; height: 118px;
  }
  .card--back .brand-name {
    left: 310px;
    top: 150px;
    font-size: 46px;
    letter-spacing: 1px;
  }
</style>
</head>
<body>
<main class="canvas">
  <section class="card card--front">
    <h1 class="brand-name">Veloran<br>Cabinets</h1>
    <div class="brand-mark" aria-hidden="true"></div>

    <h2 class="person-name">Mitchell Tarrowby</h2>
    <p class="person-role">Director Craftsman</p>

    <ul class="contact-list">
      <li class="contact-item">
        <svg class="contact-icon" viewBox="0 0 18 18" aria-hidden="true">
          <rect x="1" y="4" width="16" height="11" fill="var(--gold)"/>
          <path d="M1 4 L9 10 L17 4" fill="none" stroke="var(--card-green)" stroke-width="1.6"/>
        </svg>
        info@veloranjoinery-example.com.au
      </li>
      <li class="contact-item">
        <svg class="contact-icon" viewBox="0 0 18 18" aria-hidden="true">
          <rect x="2" y="2" width="14" height="14" fill="none" stroke="var(--gold)" stroke-width="1.6"/>
        </svg>
        @veloran.cabinets
      </li>
    </ul>
  </section>

  <section class="card card--back">
    <div class="brand-mark" aria-hidden="true"></div>
    <p class="brand-name">Veloran<br>Cabinets</p>
  </section>
</main>
</body>
</html>
```